i would like a business card to leave with customers and potential customers for electrical work and for the supply and install of reverse cycle airconditioning in the domestic and commercial market.
I own my own business and im a sole trader. I have an a'class electrical lisence and also a refrigeration lisence so i am
able to offer complete installations in airconditioning by a fully qualified and lisenced tradesman.
im looking for something that comes across as unique and professional.
i had the coluor black and some gold in mind but open to any coluors.
something like Lanterra Electrical & Refrigeration
or Lanterra Air.
i will use this design on a business card to advertise through summer to help generate installs through the busy season.

Target Market(s)

Mainly domestic house holds through summer who are in need of airconditioning and reliable information to acomadate thier cooling and heating requirements

Industry/Entity Type

Electrical

Requirements
Must have
• Business name- Lanterra
My name- Mark Delford
My mobile no- 0438 517 290
My email- mrdelford@qelvo.com.au
Installation & Decomissioning of aiconditioning split systems
LIC NO: TRK 540316
Nice to have
• Lanterra Electrical & Refrigeration

```html
<!DOCTYPE html>
<html lang="en">
<head>
<meta charset="utf-8">
<title>Lanterra Electrical &amp; Refrigeration – Business Card</title>
<link rel="stylesheet" href="https://fonts.googleapis.com/css2?family=Open+Sans:wght@700;800&family=Arimo:wght@700&display=swap">
<style>
  :root {
    --backdrop: #d3d8db;
    --card-gold: #ffc600;
    --card-black: #000000;
    --ink: #000000;
    --paper: #ffffff;
    --mark-blue: #2b8ff0;
    --badge-cyan: #6fe0fb;
  }
  * { margin: 0; padding: 0; box-sizing: border-box; }
  html, body {
    width: 1200px; height: 900px; overflow: hidden;
    background: var(--backdrop);
  }
  .stage { position: relative; width: 1200px; height: 900px; }
  .card {
    position: absolute; top: 57px; width: 450px; height: 783px;
    border-radius: 28px; overflow: hidden;
  }
  .card--front { left: 101px; background: var(--card-gold); }
  .card--back { left: 649px; background: var(--card-black); }

  .brand-dot {
    position: absolute; left: 126px; top: 0; width: 178px; height: 178px;
    border-radius: 50%; background: var(--mark-blue);
  }
  .company-name {
    position: absolute; top: 200px; width: 100%; text-align: center;
    font: 700 18px "Open Sans", sans-serif; color: var(--ink);
  }
  .wordmark { position: absolute; inset: 0; }
  .wordmark text { font-family: "Open Sans", sans-serif; font-weight: 800; }

  .contact-name {
    position: absolute; left: 200px; top: 612px; width: 220px; text-align: center;
    font: 700 29px "Arimo", sans-serif; color: var(--ink);
  }
  .contact-phone {
    position: absolute; left: 200px; top: 650px; width: 220px; text-align: center;
    font: 700 20px "Arimo", sans-serif; color: var(--ink); letter-spacing: 1px;
  }
  .contact-email {
    position: absolute; bottom: 26px; width: 100%; text-align: center;
    font: 700 17px "Arimo", sans-serif; color: var(--ink); letter-spacing: 2px;
  }

  .service-line {
    position: absolute; left: 32px; top: 30px;
    font: 700 17.5px/23px "Open Sans", sans-serif; color: var(--paper);
  }
  .cert-badge {
    position: absolute; left: 89px; top: 585px; width: 97px; height: 97px;
    background: var(--badge-cyan);
  }
  .licence {
    position: absolute; left: 31px; top: 730px;
    font: 700 20px "Arimo", sans-serif; color: var(--paper);
  }
</style>
</head>
<body>
<main class="stage">
  <section class="card card--front">
    <div class="brand-dot"></div>
    <p class="company-name">Lanterra Electrical &amp; Refrigeration</p>
    <svg class="wordmark" width="450" height="783" viewBox="0 0 450 783">
      <text x="225" y="480" text-anchor="middle" font-size="112" fill="#000"
            textLength="520" lengthAdjust="spacingAndGlyphs"
            transform="rotate(-31 225 450)">Lanterra</text>
    </svg>
    <p class="contact-name">Mark Delford</p>
    <p class="contact-phone">0438 517 290</p>
    <p class="contact-email">mrdelford@qelvo.com.au</p>
  </section>

  <section class="card card--back">
    <p class="service-line">Installation &amp; Decommissioning<br>of air-conditioning split systems</p>
    <svg class="wordmark" width="450" height="783" viewBox="0 0 450 783">
      <text x="0" y="0" text-anchor="middle" font-size="190" fill="#ffc600"
            textLength="770" lengthAdjust="spacingAndGlyphs"
            transform="translate(430 392) rotate(-90)">Lanterra</text>
    </svg>
    <div class="cert-badge" role="img" aria-label="Authorised certification badge"></div>
    <p class="licence">LIC NO: TRK 540316</p>
  </section>
</main>
</body>
</html>
```